Help our Sugar Loom find our winning design! We're looking for a business card....

We’re a Sugar Loom in NY specializing in custom-made cakes and unique desserts.
Our cakes combine flavor and art, each designed to match customer’s special event and theme.
We’d like a unique business card with a clean design that will combine French chic and artistic look & feel.
We’d like to differentiate ourselves from standard bakeries, please don’t offer cupcake images :-)
Our logo is peach-pink and brown and we’d love to use these colors ( . Another color that can be added is gold - or feel free to suggest!

Target Market(s)

Women, ages 25-55

Industry/Entity Type

Boutique

Contact Information for Business Card

Text on card:
Logo
Sugar Loom by Dana Welch

www.sugarloomsweets.com
hello@sugarloom.com
(516) 555-0147
F – sugarloomnyc
IG - sugarloom_ny

Font styles to use
Sans Serif
Script

Requirements
Must have
• Logo
• Clean look
• French chic and artistic look & feel.
Nice to have
• Damask pattern
Should not have
• Cupcake images

```html
<!DOCTYPE html>
<html lang="en">
<head>
<meta charset="utf-8">
<title>Sugar Loom – Business Card</title>
<link rel="stylesheet" href="https://fonts.googleapis.com/css2?family=Raleway:wght@400;600&display=swap">
<style>
  :root {
    --backdrop: #c6c6c6;
    --card-white: #f5f5f5;
    --pink: #f595a8;
    --cocoa: #4a4443;
    --ink: #3b3534;
    --white: #ffffff;
  }
  * { margin: 0; padding: 0; box-sizing: border-box; }
  html, body { width: 805px; height: 1200px; overflow: hidden; }
  body {
    background: var(--backdrop);
    font-family: "Raleway", sans-serif;
    display: flex; flex-direction: column; align-items: center; justify-content: center;
    gap: 120px;
  }
  .card {
    position: relative; width: 640px; height: 366px;
    background: var(--card-white);
    box-shadow: 0 14px 30px rgba(0,0,0,.18);
    overflow: hidden;
  }
  .card__bands { position: absolute; inset: 0; }
  .brand {
    position: absolute; text-align: center; color: var(--ink);
  }
  .brand__name { font-size: 30px; font-weight: 400; letter-spacing: 1px; }
  .brand__tagline { font-size: 9px; letter-spacing: 2px; text-transform: uppercase; margin-top: 6px; }
  .card--front .brand { left: 0; right: 0; top: 150px; }
  .card--back .brand { left: 0; width: 240px; top: 160px; }
  .brand__mark {
    display: inline-block; width: 8px; height: 8px; border-radius: 50%;
    background: var(--pink); vertical-align: middle; margin-right: 10px;
  }
  .details {
    position: absolute; left: 290px; right: 40px; top: 40px;
    color: var(--white); text-align: right;
  }
  .details__name { font-size: 20px; font-weight: 600; letter-spacing: 3px; }
  .details__title { font-size: 10px; letter-spacing: 2px; text-transform: uppercase; margin-top: 4px; }
  .contact { list-style: none; margin-top: 70px; }
  .contact__item {
    display: flex; justify-content: flex-end; align-items: center; gap: 10px;
    font-size: 11px; letter-spacing: .5px; height: 24px;
  }
  .contact__icon {
    width: 17px; height: 17px; background: var(--white); border-radius: 2px;
    display: flex; align-items: center; justify-content: center;
  }
</style>
</head>
<body>

<section class="card card--front" aria-label="Card front">
  <svg class="card__bands" width="640" height="366" viewBox="0 0 640 366">
    <rect x="0" y="0" width="640" height="62" fill="var(--pink)"/>
    <polygon points="0,62 400,62 400,72 640,72 640,94 380,94 380,84 0,84" fill="var(--cocoa)"/>
    <rect x="0" y="304" width="640" height="62" fill="var(--pink)"/>
    <polygon points="0,282 260,282 260,272 640,272 640,294 240,294 240,304 0,304" fill="var(--cocoa)"/>
  </svg>
  <div class="brand">
    <div class="brand__name"><span class="brand__mark"></span>Sugar Loom</div>
    <div class="brand__tagline">custom cakes &amp; desserts</div>
  </div>
</section>

<section class="card card--back" aria-label="Card back">
  <svg class="card__bands" width="640" height="366" viewBox="0 0 640 366">
    <rect x="258" y="0" width="382" height="366" fill="var(--pink)"/>
    <rect x="240" y="0" width="18" height="366" fill="var(--cocoa)"/>
    <rect x="622" y="0" width="18" height="366" fill="var(--cocoa)"/>
  </svg>
  <div class="brand">
    <div class="brand__name" style="font-size:24px"><span class="brand__mark"></span>Sugar Loom</div>
    <div class="brand__tagline">custom cakes &amp; desserts</div>
  </div>
  <div class="details">
    <div class="details__name">DANA WELCH</div>
    <div class="details__title">Owner &amp; Cake Artist</div>
    <ul class="contact">
      <li class="contact__item">(516) 555-0147
        <span class="contact__icon"><svg width="11" height="11" viewBox="0 0 24 24"><path d="M6.6 10.8a15 15 0 0 0 6.6 6.6l2.2-2.2a1 1 0 0 1 1-.25 11.4 11.4 0 0 0 3.6.57 1 1 0 0 1 1 1V20a1 1 0 0 1-1 1A17 17 0 0 1 3 4a1 1 0 0 1 1-1h3.5a1 1 0 0 1 1 1c0 1.25.2 2.45.57 3.57a1 1 0 0 1-.25 1z" fill="var(--pink)"/></svg></span></li>
      <li class="contact__item">hello@sugarloom.com
        <span class="contact__icon"><svg width="11" height="11" viewBox="0 0 24 24"><rect x="2" y="5" width="20" height="14" rx="1" fill="none" stroke="var(--pink)" stroke-width="2.5"/><path d="M2 6l10 7 10-7" fill="none" stroke="var(--pink)" stroke-width="2.5"/></svg></span></li>
      <li class="contact__item">www.sugarloomsweets.com
        <span class="contact__icon"><svg width="11" height="11" viewBox="0 0 24 24"><circle cx="12" cy="12" r="9" fill="none" stroke="var(--pink)" stroke-width="2.5"/><path d="M3 12h18M12 3c3 3 3 15 0 18M12 3c-3 3-3 15 0 18" fill="none" stroke="var(--pink)" stroke-width="2"/></svg></span></li>
      <li class="contact__item">214 Mott Street, New York, NY 10012
        <span class="contact__icon"><svg width="11" height="11" viewBox="0 0 24 24"><path d="M12 2a7 7 0 0 0-7 7c0 5 7 13 7 13s7-8 7-13a7 7 0 0 0-7-7zm0 9.5A2.5 2.5 0 1 1 12 6.5a2.5 2.5 0 0 1 0 5z" fill="var(--pink)"/></svg></span></li>
    </ul>
  </div>
</section>

</body>
</html>
```